African homeware retailer needs a web page design

We need a web page design for a new homeware and accessories store based in Johannesburg, South Africa. Our store carries modern African inspired items from designers that support social development and poverty alleviation initiatives. We have a particular preference for outfits that are centred on the empowerment of women.

Our business celebrates the skill, design and product of African craft and the work of designers looking to take that forward in a socially beneficial way (creating employment, developing skills, supporting local crafts people etc). We aim to carry items and inspirations from all over the African continent.

We would like to see a design that communicates African beauty and elegance without the typical tribal references that are made in reference to African craft or art.

We would like the web page to be stylish, uncomplicated, modern, captivating and appealing to the discerning customer. A similar value proposition is that of http://www.marlowtenwick.example/.

This is an e-commerce website which must be attractive to both individual buyers and design professionals so the website needs to look professional.

Here are links to some websites we like:
http://www.quenbyhollis.example/
http://www.dravelo.example/

Our logo is attached to the brief.

Target Market(s)

Our target market is female, age 20-50. However should not alienate the design conscious male customer therefore

Industry/Entity Type

E-Commerce

Requirements
Must have
• - A featured product banner which includes a photograph and text. This should be easy to edit as we will be changing the featured product regularly
- An easily expendable products section with categories. Examples of categories could be cushions, bedding, crockery etc. Should be easy to add new categories as well as new product pictures
- Home/landing page should be uncluttered
- Should use the logo and should be easy to change the logo which we have in various colour combinations. We plan to change the logo colours depending on circumstance e.g. make it red and white around Valentines day (similar to the way Vintrel frequently changes the logo on their landing page)

```html
<!DOCTYPE html>
<html lang="en">
<head>
<meta charset="utf-8">
<title>Lumela Home — homeware &amp; accessories</title>
<link rel="stylesheet" href="https://fonts.googleapis.com/css2?family=Open+Sans:wght@400;600;700&family=Noto+Serif:ital@1&display=swap">
<style>
:root{
  --teal:#1b7a78;
  --brand-red:#e0461e;
  --plum:#5a3e45;
  --coral:#e05a50;
  --amber:#f7a940;
  --mint:#7ebd9a;
  --mint-light:#cfe6dc;
  --card-plum:#6e4f55;
  --card-coral:#e06a60;
  --card-amber:#f7b758;
  --text:#4a4a4a;
  --muted:#6a6a6a;
  --line:#d8d8d8;
  --page-bg:#f1f2f4;
}
*{box-sizing:border-box;margin:0;padding:0}
html,body{width:1019px;height:1200px;overflow:hidden}
body{background:var(--page-bg);font-family:"Open Sans",Arial,sans-serif;color:var(--text);position:relative}
.page{position:absolute;left:111px;top:0;width:797px;height:1200px;background:#fff;border-left:1px solid #e4e4e4;border-right:1px solid #e4e4e4}
.abs{position:absolute}
/* header */
.brand{left:137px;top:30px;display:flex;align-items:center;gap:12px}
.brand-square{width:52px;height:52px;background:var(--brand-red)}
.brand-name{font-size:27px;font-weight:700;color:var(--teal);letter-spacing:2px;line-height:1}
.search{left:438px;top:67px;width:217px;height:26px;border:1px solid var(--line);display:flex}
.search span{flex:1;font-size:10px;color:#888;padding:6px 9px}
.search-btn{width:29px;height:100%;background:#f7b040;display:flex;align-items:center;justify-content:center}
.social{display:flex;gap:6px}
.social-item{width:26px;height:26px;border:1.5px solid var(--mint);border-radius:50%;color:var(--mint);font-size:7px;font-weight:600;display:flex;align-items:center;justify-content:center}
.header-social{left:668px;top:67px}
.agent{left:771px;top:68px;width:111px;height:23px;background:var(--mint-light);font-size:11px;font-weight:600;color:#333;display:flex;align-items:center;justify-content:center}
/* nav */
.nav-link{top:132px;font-size:11.5px;font-weight:700;line-height:15px;color:var(--brand-red);text-decoration:none}
.nav-link.current{color:var(--teal)}
.nav-sep{top:132px;font-size:11px;line-height:15px;color:#ccc}
.nav-btn{top:125px;height:29px;color:#fff;font-size:11.5px;font-weight:700;display:flex;align-items:center;justify-content:center}
.btn-shop{left:547px;width:89px;background:var(--plum)}
.btn-lorem{left:639px;width:102px;background:var(--coral)}
.btn-join{left:744px;width:70px;background:var(--amber)}
.blog{left:821px;top:121px}
/* hero */
.hero{left:137px;top:170px;width:745px;height:326px;background:radial-gradient(ellipse at 55% 55%,#5a5a5e 0%,#2a2a2c 45%,#101010 100%)}
.hero-accent{left:330px;top:255px;width:230px;height:110px;background:radial-gradient(ellipse,rgba(214,110,30,.55),rgba(214,110,30,0) 70%)}
.hero-text{left:268px;top:206px;font-family:"Noto Serif",Georgia,serif;font-style:italic;font-size:20px;line-height:27px;color:#fff}
.dots{left:467px;top:506px;display:flex;gap:10px}
.dot{width:11px;height:11px;transform:rotate(45deg);background:var(--brand-red);margin:3px}
.dot.active{background:var(--teal)}
/* category cards */
.card{top:543px;width:237px;height:180px;border:2px solid;text-align:center}
.card h2{font-size:22px;font-weight:700;margin-top:5px;letter-spacing:.5px}
.card-img{width:90px;height:64px;margin:6px auto 0}
.card p{font-size:9.5px;line-height:12px;color:var(--muted);margin-top:9px}
.card-btn{width:141px;height:30px;margin:8px auto 0;background:var(--mint);color:#fff;font-size:13px;font-weight:700;display:flex;align-items:center;justify-content:center}
.card-cushions{left:137px;border-color:var(--card-plum)}
.card-cushions h2{color:var(--card-plum)}
.card-bedding{left:391px;border-color:var(--card-coral)}
.card-bedding h2{color:var(--card-coral)}
.card-crockery{left:645px;border-color:var(--card-amber)}
.card-crockery h2{color:var(--card-amber)}
/* lower sections */
.section-title{top:756px;width:237px;font-size:11px;color:#333;padding-bottom:6px;border-bottom:1.5px solid var(--line)}
.section-title::after{content:"";position:absolute;left:0;bottom:-2px;width:64px;height:3px;background:var(--teal)}
.catalog{left:155px;top:802px;width:180px;height:122px;background:linear-gradient(120deg,#8a7b68 0%,#a4907a 40%,#b9533b 60%,#3d5a7a 100%)}
.news-square{left:396px;top:810px;width:32px;height:32px;background:var(--brand-red)}
.news-text{left:441px;top:813px;width:180px;font-size:9.5px;line-height:12px;color:var(--muted)}
.email{left:392px;top:862px;width:236px;height:26px;border:1px solid var(--line);display:flex}
.email span{flex:1;font-size:10px;color:#777;padding:6px 8px}
.email-btn{width:29px;background:#f7b040;display:flex;align-items:center;justify-content:center}
.artisan{left:646px;width:236px;display:flex;gap:17px}
.artisan-photo{width:45px;height:45px;flex:none;background:linear-gradient(160deg,#6a6a6a,#b89a86)}
.artisan h3{font-size:10px;font-weight:600;color:#222;margin-top:1px;white-space:nowrap}
.artisan p{font-size:10px;line-height:13px;color:var(--text);margin-top:5px}
.artisan-rule{left:646px;top:926px;width:229px;height:1px;background:var(--line)}
/* footer */
.rule{left:137px;width:745px;height:1.5px;background:var(--line)}
.foot-title{top:969px;font-size:12.5px;font-weight:700;color:#333}
.links{top:996px;display:grid;grid-template-columns:85px 80px;row-gap:10px;font-size:10px;color:#444}
.field{left:346px;width:135px;border:1.5px solid #ccc;border-radius:2px;font-size:10px;font-style:italic;color:#888;padding:2px 8px}
.submit{left:346px;top:1088px;width:54px;height:19px;background:var(--brand-red);color:#fff;font-size:11px;font-weight:600;border-radius:2px;display:flex;align-items:center;justify-content:center}
.pay{top:996px;height:16px;font-size:7px;font-weight:600;border:1px solid #ddd;color:#555;display:flex;align-items:center;justify-content:center;width:28px}
.pay-big{top:1029px;font-size:13px;font-weight:700;color:#2a4a8a}
.foot-social{left:562px;top:1084px;gap:11px}
.foot-social .social-item{width:21px;height:21px;font-size:6px}
.foot-brand{left:774px;top:982px;width:108px;height:125px;background:#f7f7f7;display:flex;flex-direction:column;align-items:center;justify-content:center;gap:12px}
.foot-brand .brand-square{width:40px;height:40px}
.foot-brand .brand-name{font-size:15px;color:var(--brand-red);text-align:center;line-height:1.1}
.copyright{left:137px;top:1134px;width:745px;text-align:center;font-size:10px;color:#555}
</style>
</head>
<body>
<div class="page"></div>

<header>
  <div class="abs brand"><div class="brand-square"></div><div class="brand-name">LUMELA<br>HOME</div></div>
  <div class="abs search"><span>SEARCH OUR SITE</span><div class="search-btn"><svg width="11" height="11" viewBox="0 0 11 11"><circle cx="4.5" cy="4.5" r="3.3" fill="none" stroke="#fff" stroke-width="1.5"/><line x1="7" y1="7" x2="10" y2="10" stroke="#fff" stroke-width="1.6"/></svg></div></div>
  <div class="abs social header-social"><div class="social-item">Folk</div><div class="social-item">Chirp</div><div class="social-item">Pinna</div></div>
  <div class="abs agent">AGENT SIGN-IN</div>
  <nav>
    <a class="abs nav-link current" href="#" style="left:137px">HOME</a>
    <span class="abs nav-sep" style="left:197px">|</span>
    <a class="abs nav-link" href="#" style="left:224px">ABOUT US</a>
    <span class="abs nav-sep" style="left:309px">|</span>
    <a class="abs nav-link" href="#" style="left:337px">PRODUCTS</a>
    <span class="abs nav-sep" style="left:426px">|</span>
    <a class="abs nav-link" href="#" style="left:453px">CONTACT US</a>
  </nav>
  <div class="abs nav-btn btn-shop">SHOP NOW</div>
  <div class="abs nav-btn btn-lorem">LOREM IPSAM</div>
  <div class="abs nav-btn btn-join">JOIN US</div>
  <svg class="abs blog" width="62" height="36" viewBox="0 0 62 36"><path d="M14 2 H48 A13 13 0 0 1 48 32 H18 L2 35 L9 27 A13 13 0 0 1 14 2 Z" fill="var(--mint)"/><text x="34" y="23" font-family="Open Sans,sans-serif" font-size="16" fill="#fff" text-anchor="middle">blog</text></svg>
</header>

<section>
  <div class="abs hero" role="img" aria-label="Featured product photo: beaded wire motorcycle sculpture on black"></div>
  <div class="abs hero-accent"></div>
  <p class="abs hero-text">Lorem ipsum dolor sit<br>amet, consectet<br>adipisc eli.</p>
  <div class="abs dots"><div class="dot"></div><div class="dot active"></div><div class="dot"></div><div class="dot"></div></div>
</section>

<section>
  <div class="abs card card-cushions"><h2>CUSHIONS</h2><div class="card-img" role="img" aria-label="Patterned cushions" style="background:linear-gradient(135deg,#c23a1c,#e98a2a 50%,#3a4ea0)"></div><p>Lorem ipsum dolor sit amet, consectet<br>adipiscing elit, sed diam nonum</p><div class="card-btn">BUY NOW</div></div>
  <div class="abs card card-bedding"><h2>BEDDING</h2><div class="card-img" role="img" aria-label="White made bed" style="background:linear-gradient(180deg,#f4f4f4,#cfcfcf)"></div><p>Lorem ipsum dolor sit amet, consectet<br>adipiscing elit, sed diam nonum</p><div class="card-btn">BUY NOW</div></div>
  <div class="abs card card-crockery"><h2>CROCKERY</h2><div class="card-img" role="img" aria-label="Carved wooden bowls and spoons" style="background:radial-gradient(ellipse,#a55a2a,#e8c8a8 75%,#fff)"></div><p>Lorem ipsum dolor sit amet, consectet<br>adipiscing elit, sed diam nonum</p><div class="card-btn">BUY NOW</div></div>
</section>

<section>
  <div class="abs section-title" style="left:137px">VIEW OUR CATALOG</div>
  <div class="abs section-title" style="left:392px">DON'T MISS OUT AGAIN</div>
  <div class="abs section-title" style="left:646px">MEET OUR ARTISTIAN</div>
  <div class="abs catalog" role="img" aria-label="Two craft magazine covers"></div>
  <div class="abs news-square"></div>
  <p class="abs news-text">Lorem ipsum dolor sit amet, consectet adipiscing elit, sed diam nonummy</p>
  <div class="abs email"><span>ENTER EMAIL ADDRESS</span><div class="email-btn"><svg width="12" height="9" viewBox="0 0 12 9"><rect x=".5" y=".5" width="11" height="8" fill="none" stroke="#fff"/><path d="M.5 .5 L6 5 L11.5 .5" fill="none" stroke="#fff"/></svg></div></div>
  <div class="abs artisan" style="top:804px"><div class="artisan-photo" role="img" aria-label="Portrait of an artisan"></div><div><h3>Lorem ipsum dolor sitamet conse</h3><p>Lorem ipsum dolor sit amet,<br>consectet adipisc eli sed</p></div></div>
  <div class="abs artisan" style="top:866px"><div class="artisan-photo" role="img" aria-label="Portrait of an artisan"></div><div><h3>Lorem ipsum dolor sitamet conse</h3><p>Lorem ipsum dolor sit amet,<br>consectet adipisc eli sed</p></div></div>
  <div class="abs artisan-rule"></div>
</section>

<footer>
  <div class="abs rule" style="top:953px"></div>
  <div class="abs foot-title" style="left:137px">Quick Links</div>
  <div class="abs links" style="left:137px"><span>HOME</span><span>JOIN US</span><span>ABOUT US</span><span>BLOG</span><span>PRODUCTS</span><span>SITE MAP</span><span>CONTACT US</span><span></span><span>SHOP NOW</span><span></span></div>
  <div class="abs foot-title" style="left:347px">Quick Contact</div>
  <div class="abs field" style="top:995px;height:19px">Name</div>
  <div class="abs field" style="top:1021px;height:19px">Email</div>
  <div class="abs field" style="top:1047px;height:35px">Message</div>
  <div class="abs submit">Submit</div>
  <div class="abs foot-title" style="left:563px">We Accept</div>
  <div class="abs pay" style="left:562px">Vexa</div>
  <div class="abs pay" style="left:597px">Marda</div>
  <div class="abs pay" style="left:633px">Amvo</div>
  <div class="abs pay" style="left:668px">Diskra</div>
  <div class="abs pay-big" style="left:563px">PayWell</div>
  <div class="abs pay-big" style="left:637px;color:#222;font-size:11px;top:1031px">DebitLine</div>
  <div class="abs foot-title" style="left:561px;top:1064px">Connect With Us</div>
  <div class="abs social foot-social"><div class="social-item">Folk</div><div class="social-item">Chirp</div><div class="social-item">Pinna</div></div>
  <div class="abs foot-brand"><div class="brand-square"></div><div class="brand-name">LUMELA<br>HOME</div></div>
  <div class="abs rule" style="top:1124px"></div>
  <p class="abs copyright">© 2014 Lumelahome. All Rights Reserved.</p>
</footer>
</body>
</html>
```